Business Card Design Project : Ridgeline Press

In preparation for market launch, Tamarind's Ridgeline Press require the development of a business card. Ridgeline Press is a Community online publishing web portal. We provide the the city of Whistler located in B.C. (Canada) business directories, News, Classified ads, News, Events and blogs etc.

The main focus of the brand is to help local businesses to corporate with their online advertisement and marketing. Meeting our clients face to face is a must (B2B).

Target Market(s)

The target market is B2B customers. Business Owners to Marketing, advertising Managers

Industry/Entity Type

Business

Requirements
Must have
• - The business card will be two sided.
the BACK side will have our logo which consist of (icon, url,slogan) submited. The logo will be middle and centred.

The FRONT side should have company details:

Company Legal Name: TAMARIND RIDGELINE MEDIA

Owen Farsk
Director of Sales & Marketing

www.tamarindridgeline.biz
owen@tamarindridgeline.biz

Phone: 604 317 8842
#2714 - 582 E. Halvern St.
Vancouver, B.C. V7K2R4 Canada
Nice to have
• - For the "FRONT" side of our business card. You can separate or re-arrange with our logo components (icon, logo,slogan). It does not have to be together.

Also our company legal name is rather long so arrange or organize the name in a way to make it shorter. Your experience and creativity will have to come in play.
Should not have
• should not have other colors beside logo color and black text (2 colors). Also nothing Three dimensional

```html
<!DOCTYPE html>
<html lang="en">
<head>
<meta charset="utf-8">
<title>Tamarind Ridgeline Media – Business Card</title>
<link rel="stylesheet" href="https://fonts.googleapis.com/css2?family=Open+Sans:wght@400;600;700&display=swap">
<style>
  :root {
    --brand-blue: #1f7cc1;
    --ink: #1a1a1a;
    --rule-dark: #3a3a3a;
    --paper: #ffffff;
    --backdrop: #eceef0;
  }
  * { box-sizing: border-box; margin: 0; padding: 0; }
  html, body { width: 756px; height: 1200px; overflow: hidden; }
  body {
    background: var(--backdrop);
    font-family: "Open Sans", sans-serif;
    color: var(--ink);
    position: relative;
  }
  .card {
    position: absolute;
    left: 58px;
    width: 640px;
    height: 366px;
    background: var(--paper);
    overflow: hidden;
  }

  /* Back side */
  .card-back { top: 150px; }
  .back-brand {
    position: absolute;
    left: 0; right: 0; top: 0;
    height: 250px;
    display: flex;
    align-items: center;
    justify-content: center;
    gap: 18px;
  }
  .brand-mark {
    width: 34px; height: 34px;
    border-radius: 50%;
    background: var(--brand-blue);
  }
  .back-brand .brand-name {
    font-weight: 600;
    font-size: 36px;
    color: var(--brand-blue);
  }
  .back-rule {
    position: absolute;
    left: 0; right: 0; top: 250px;
    height: 7px;
    background: var(--rule-dark);
  }
  .back-band {
    position: absolute;
    left: 0; right: 0; top: 257px; bottom: 0;
    background: var(--brand-blue);
    display: flex;
    align-items: center;
    justify-content: center;
  }
  .back-band .url {
    color: var(--paper);
    font-size: 21px;
    letter-spacing: 0.3px;
  }

  /* Front side */
  .card-front { top: 650px; }
  .front-brand {
    position: absolute;
    left: 28px; top: 0; bottom: 0;
    width: 270px;
    display: flex;
    align-items: center;
    justify-content: center;
    gap: 10px;
  }
  .front-brand .brand-mark { width: 16px; height: 16px; }
  .front-brand .brand-name {
    font-weight: 700;
    font-size: 19px;
    color: var(--brand-blue);
    white-space: nowrap;
  }
  .divider {
    position: absolute;
    left: 316px; top: 50px;
    width: 2px; height: 266px;
    background: var(--brand-blue);
  }
  .details {
    position: absolute;
    left: 346px; top: 56px; right: 20px;
  }
  .person-name {
    font-weight: 700;
    font-size: 27px;
    color: var(--brand-blue);
    line-height: 1.1;
  }
  .person-title {
    font-size: 15px;
    margin-top: 4px;
  }
  .contact-list { list-style: none; }
  .contact-list li {
    display: flex;
    align-items: flex-start;
    gap: 14px;
    font-size: 13.5px;
    line-height: 1.5;
  }
  .contact-list svg { width: 15px; height: 15px; flex: none; margin-top: 3px; fill: var(--ink); }
  .address-list { margin-top: 38px; }
  .reach-list { margin-top: 36px; }
  .reach-list li + li { margin-top: 4px; }
</style>
</head>
<body>

<section class="card card-back" aria-label="Card back">
  <div class="back-brand">
    <span class="brand-mark" aria-hidden="true"></span>
    <span class="brand-name">Tamarind Ridgeline Media</span>
  </div>
  <div class="back-rule"></div>
  <div class="back-band">
    <span class="url">www.tamarindridgeline.biz</span>
  </div>
</section>

<section class="card card-front" aria-label="Card front">
  <div class="front-brand">
    <span class="brand-mark" aria-hidden="true"></span>
    <span class="brand-name">Tamarind Ridgeline Media</span>
  </div>
  <div class="divider"></div>
  <div class="details">
    <h1 class="person-name">Owen Farsk</h1>
    <p class="person-title">Director of Sales &amp; Marketing</p>

    <ul class="contact-list address-list">
      <li>
        <svg viewBox="0 0 16 16" aria-hidden="true"><path d="M0 0h16v16H0z" fill="none"/><path d="M1 1h14v14H1z" fill="none" stroke="#1a1a1a" stroke-width="1.6"/><path d="M8 3.5 3.5 7.5h1.3V12h2.4V9.5h1.6V12h2.4V7.5h1.3z"/></svg>
        <span>#2714 - 582 E. Halvern St.<br>Vancouver, B.C. V7K2R4 Canada</span>
      </li>
    </ul>

    <ul class="contact-list reach-list">
      <li>
        <svg viewBox="0 0 16 16" aria-hidden="true"><circle cx="8" cy="8" r="7.5"/><path d="M5.2 4h1.6l.7 2-1 .8a6 6 0 0 0 2.7 2.7l.8-1 2 .7v1.6c0 .5-.4.9-.9.9A7.3 7.3 0 0 1 4.3 4.9c0-.5.4-.9.9-.9z" fill="#fff"/></svg>
        <span>604 317 8842</span>
      </li>
      <li>
        <svg viewBox="0 0 16 16" aria-hidden="true"><path d="M1 3.5h14v9H1z"/><path d="M1.5 4 8 9l6.5-5" fill="none" stroke="#fff" stroke-width="1.2"/></svg>
        <span>owen@tamarindridgeline.biz</span>
      </li>
      <li>
        <svg viewBox="0 0 16 16" aria-hidden="true"><circle cx="8" cy="8" r="7.5"/><path d="M.8 8h14.4M8 .8c-3 3.5-3 10.9 0 14.4M8 .8c3 3.5 3 10.9 0 14.4" fill="none" stroke="#fff" stroke-width="1"/></svg>
        <span>www.tamarindridgeline.biz</span>
      </li>
    </ul>
  </div>
</section>

</body>
</html>
```